Bourbon label design for bourbon brand. Looking to freshen our current label.

I need a Bourbon label design for our rebranded Bourbon bottle. Label should include picture of our horse and our logo on the bottle. Front Label is 3.5 inches wide and 6 inches tall, back label is 4 inches tall and 3 inches wide. Back label can be a simple plain logo like the one in the brief. I have included a design of our current bottle and label. We want to stay close to the current color schemes but want a fresh rebrand of the design. The label needs to be the correct size on a tall bottle like pictured.

Target Market(s)

Our Bourbon members, 30-50 year old males

Requirements
Must have
• Picture of our horse, our B logo , straight Bourbon whiskey on the front. Room to edit text on the back label.

```html
<!DOCTYPE html>
<html lang="en">
<head>
<meta charset="UTF-8">
<title>Nightfall Straight Bourbon Whiskey – Label Set</title>
<link href="https://fonts.googleapis.com/css2?family=New+Rocker&family=Roboto+Condensed:wght@700&family=Montserrat:wght@400;500;700&display=swap" rel="stylesheet">
<style>
  :root {
    --canvas: #ffffff;
    --label: #000000;
    --ink: #ffffff;
    --ink-soft: #c9c9c9;
    --gold: #c9a86a;
    --illo-light: #d8d8d8;
    --illo-dark: #3a3a3a;
  }
  * { margin: 0; padding: 0; box-sizing: border-box; }
  html, body { width: 1200px; height: 1200px; overflow: hidden; background: var(--canvas); }
  .canvas { position: relative; width: 1200px; height: 1200px; }

  .label { position: absolute; background: var(--label); color: var(--ink); overflow: hidden; }
  .label > * { position: absolute; }

  /* Front label */
  .front-label { left: 120px; top: 205px; width: 460px; height: 789px; font-family: "New Rocker", serif; }
  .horse-illustration {
    left: 164px; top: 28px; width: 136px; height: 266px;
    background: radial-gradient(ellipse at 50% 40%, var(--illo-light) 0%, #9a9a9a 50%, var(--illo-dark) 85%, var(--label) 100%);
    border-radius: 40% 40% 30% 30% / 25% 25% 12% 12%;
  }
  .est-mark { width: 64px; top: 145px; text-align: center; font-size: 20px; color: var(--ink-soft); line-height: 26px; }
  .est-mark::before, .est-mark::after {
    content: ""; position: absolute; left: 0; right: 0; height: 2px;
    background: linear-gradient(90deg, transparent, var(--gold), transparent);
  }
  .est-mark::before { top: -2px; }
  .est-mark::after { bottom: -3px; }
  .est-left { left: 78px; }
  .est-right { left: 316px; }

  .brand-title { left: 0; width: 100%; top: 318px; text-align: center; font-size: 60px; line-height: 66px; font-weight: 400; }
  .brand-subtitle { left: 0; width: 100%; top: 388px; text-align: center; font-size: 20px; line-height: 24px; color: var(--ink-soft); }

  .side-note { top: 478px; width: 80px; text-align: center; font-size: 13px; line-height: 13px; color: var(--ink); }
  .side-left { left: 49px; }
  .side-right { left: 323px; }

  .front-mark { left: 170px; top: 448px; width: 120px; text-align: center; }
  .mark-circle { display: block; width: 46px; height: 46px; margin: 0 auto 6px; border: 3px solid var(--ink); border-radius: 50%; }
  .mark-name { font-size: 15px; letter-spacing: 1px; }

  .series-name { left: 0; width: 100%; top: 546px; text-align: center; font-size: 21px; color: var(--ink-soft); }

  .spec { top: 616px; width: 90px; text-align: center; font-size: 16px; color: var(--ink-soft); }
  .spec-box { display: block; width: 72px; height: 43px; margin: 6px auto 0; background: var(--ink); }
  .spec-barrel { left: 42px; }
  .spec-aged { left: 184px; }
  .spec-abv { left: 327px; }
  .years { left: 0; width: 100%; top: 686px; text-align: center; font-size: 16px; color: var(--ink-soft); }
  .volume { left: 0; width: 100%; top: 742px; text-align: center; font-size: 17px; }

  /* Back label */
  .back-label { left: 660px; top: 336px; width: 395px; height: 527px; text-align: center; }
  .back-mark { left: 0; width: 100%; top: 28px; }
  .back-mark .mark-circle { width: 40px; height: 40px; margin-bottom: 8px; border-width: 3px; }
  .company-name { font-family: "Montserrat", sans-serif; font-weight: 500; font-size: 18px; line-height: 18px; letter-spacing: 0.5px; }
  .company-sub { display: flex; align-items: center; justify-content: center; gap: 6px; margin-top: 3px; font-family: "Montserrat", sans-serif; font-size: 7px; letter-spacing: 4px; }
  .company-sub::before, .company-sub::after { content: ""; width: 26px; height: 1px; background: var(--ink); }

  .edition { left: 0; width: 100%; top: 134px; font-family: "Roboto Condensed", sans-serif; font-weight: 700; font-size: 18px; line-height: 21px; }
  .story { left: 16px; right: 16px; top: 203px; font-family: "Roboto Condensed", sans-serif; font-weight: 700; font-size: 11.5px; line-height: 15.7px; }
  .producer { left: 0; width: 100%; top: 332px; font-family: "Roboto Condensed", sans-serif; font-weight: 700; font-size: 11.5px; line-height: 15.7px; }
  .website { left: 0; width: 100%; top: 372px; font-family: "Roboto Condensed", sans-serif; font-weight: 700; font-size: 19px; line-height: 24px; }
  .warning { left: 56px; width: 283px; top: 428px; text-align: justify; font-family: "Montserrat", sans-serif; font-size: 8.2px; line-height: 14px; letter-spacing: 0.9px; color: var(--ink-soft); }
  .warning strong { font-weight: 700; color: var(--ink); }
</style>
</head>
<body>
<main class="canvas">

  <section class="label front-label" aria-label="Front label">
    <div class="horse-illustration" role="img" aria-label="Illustration of the stable's racehorse and jockey galloping toward the viewer, in black and white"></div>
    <div class="est-mark est-left">EST</div>
    <div class="est-mark est-right">2016</div>
    <h1 class="brand-title">NIGHTFALL</h1>
    <p class="brand-subtitle">STRAIGHT BOURBON WHISKEY</p>
    <p class="side-note side-left">SINGLE<br>BARREL</p>
    <div class="front-mark">
      <span class="mark-circle"></span>
      <span class="mark-name">NIGHTFALL</span>
    </div>
    <p class="side-note side-right">STRAIGHT<br>BARREL</p>
    <p class="series-name">WINNERS SERIES</p>
    <div class="spec spec-barrel">BARREL<span class="spec-box"></span></div>
    <div class="spec spec-aged">AGED<span class="spec-box"></span></div>
    <div class="spec spec-abv">ALC/VOL<span class="spec-box"></span></div>
    <p class="years">YEARS</p>
    <p class="volume">750ML</p>
  </section>

  <section class="label back-label" aria-label="Back label">
    <div class="back-mark">
      <span class="mark-circle"></span>
      <p class="company-name">NIGHTFALL<br>BARREL</p>
      <p class="company-sub">COMPANY</p>
    </div>
    <p class="edition">Winners Séries<br>Silver Tempest Edition<br>Single Barrel No. 45</p>
    <p class="story">The Nightfall Racing Winners Series honors the horses who have<br>brought home victories for our stable.<br>This editions celebrates Silver Tempest<br>and her maiden victory on May 28, 2021. Raise a glass to<br>her incredible career with this non chill filtered single barrel<br>crafted in her honor.<br>Here's to Silver Tempest - a true champions!</p>
    <p class="producer">Bottled by Riverbend Whiskey Co., Louisville Kentucky<br>Distilled in Bardstown, Kentucky</p>
    <p class="website">NIGHTFALL-SPIRITS.COM<br>750ml.</p>
    <p class="warning"><strong>GOVERNMENT WARNING:</strong> (1) According tho the Surgeon General, women should not drink alcoholic beverages during pregnancy because of the risk of birth defects. (2) Consumption of alcoholic bevererages impairs your ability to drive a car or operate machinry, and may cause health problems.</p>
  </section>

</main>
</body>
</html>
```